Brell Stone Company Business Cards

Front and Back Business Card - logo and text setup - cool design. I need workable photoshop or illustrator files so I can setup each employee card with design that is created
Updates

Hi everyone, thank you for the great entries. Please no more white and blue cards - there are so many already - black and silver only now please. thanks!

Target Market(s)

Construction Industry - Facility Managers

Industry/Entity Type

Construction

Contact Information for Business Card

I really like contemporary simplistic looks - clean neat....not opposed to seeing some black backrounds

Requirements
Must have
• Logo/website address with design on front only - www.brellstone-example.com (logo attached)
• Back:
• Name/Title/Company Address/Phone/email address
Nice to have
• Cool design
Should not have
• Nothing gimmicky like Fire or Water - since we are a Fire Protection company - it has all been done

```html
<!DOCTYPE html>
<html lang="en">
<head>
<meta charset="utf-8">
<title>Brell Stone Company – Business Card</title>
<link rel="stylesheet" href="https://fonts.googleapis.com/css2?family=Jost:wght@300&family=Roboto:wght@400;700;900&family=Cinzel:wght@400;700&display=swap">
<style>
  :root {
    --page: #ffffff;
    --ink: #1a1a1a;
    --muted: #555555;
    --accent: #ec4a33;
    --accent-top: #f05c2b;
    --accent-bottom: #e83e3b;
    --navy: #1d3a78;
    --dark-top: #2f2f31;
    --dark-bottom: #060607;
    --edge: #9a9a9a;
  }
  * { margin: 0; padding: 0; box-sizing: border-box; }
  html, body { width: 1200px; height: 1200px; overflow: hidden; background: var(--page); }
  body { position: relative; font-family: "Roboto", Arial, sans-serif; }

  .side-label {
    position: absolute; top: 440px; width: 463px; text-align: center;
    font-family: "Jost", "Futura", sans-serif; font-weight: 300; font-size: 33px;
    color: var(--ink); letter-spacing: 0.5px;
  }
  .side-label.front { left: 64px; }
  .side-label.back { left: 674px; }

  .card { position: absolute; top: 490px; width: 463px; height: 264px; overflow: hidden; }
  .card.front { left: 64px; background: linear-gradient(180deg, var(--dark-top), var(--dark-bottom)); }
  .card.back { left: 674px; background: #fff; border: 1px solid var(--edge); }

  .card .accent-bar { position: absolute; top: 0; bottom: 0; width: 9px; background: var(--accent); }
  .card.front .accent-bar { left: 10px; }
  .card.back .accent-bar { left: 8px; }

  .card .ribbon { position: absolute; left: 0; top: 0; width: 463px; height: 264px; }

  .wordmark { position: absolute; font-weight: 900; letter-spacing: -0.3px; }
  .card.front .wordmark { left: 26px; top: 108px; font-size: 30px; color: #ffffff; }
  .card.back .wordmark { left: 38px; top: 34px; font-size: 24px; color: var(--navy); }

  .website { position: absolute; left: 24px; top: 200px; font-size: 17px; color: #ffffff; font-weight: 400; }

  .person-name {
    position: absolute; left: 38px; top: 110px; font-family: "Cinzel", Georgia, serif;
    font-size: 21px; color: var(--accent); letter-spacing: 0.5px;
  }
  .person-name strong { font-weight: 700; }
  .job-title { position: absolute; left: 38px; top: 136px; font-size: 11px; color: var(--muted); }

  .contact-list { position: absolute; left: 38px; top: 181px; list-style: none; }
  .contact-list li { display: flex; align-items: center; height: 13.2px; font-size: 10.5px; color: var(--muted); white-space: nowrap; }
  .contact-list svg { width: 8px; height: 8px; margin-right: 5px; flex: none; }
  .contact-list b { color: var(--ink); font-weight: 700; margin-right: 3px; }
</style>
</head>
<body>
  <div class="side-label front">FRONT</div>
  <div class="side-label back">BACK</div>

  <section class="card front" aria-label="Card front">
    <svg class="ribbon" viewBox="0 0 463 264" aria-hidden="true">
      <defs>
        <linearGradient id="ribbonFront" x1="0" y1="0" x2="0" y2="1">
          <stop offset="0" stop-color="var(--accent-top)"/>
          <stop offset="1" stop-color="var(--accent-bottom)"/>
        </linearGradient>
      </defs>
      <polygon points="366,0 424,0 424,58 438,72 438,166 424,180 424,264 366,264 366,178 382,162 382,74 366,58"
               fill="url(#ribbonFront)" stroke="#b8b8b8" stroke-width="1.5"/>
    </svg>
    <div class="accent-bar"></div>
    <div class="wordmark">Brell Stone</div>
    <div class="website">www.brellstone-example.com</div>
  </section>

  <section class="card back" aria-label="Card back">
    <svg class="ribbon" viewBox="0 0 463 264" aria-hidden="true">
      <defs>
        <linearGradient id="ribbonBack" x1="0" y1="0" x2="0" y2="1">
          <stop offset="0" stop-color="var(--accent-top)"/>
          <stop offset="1" stop-color="var(--accent-bottom)"/>
        </linearGradient>
      </defs>
      <polygon points="370,0 428,0 428,58 442,72 442,166 428,180 428,264 370,264 370,178 386,162 386,74 370,58"
               fill="url(#ribbonBack)" stroke="#8f8f8f" stroke-width="1.5"/>
    </svg>
    <div class="accent-bar"></div>
    <div class="wordmark">Brell Stone</div>
    <div class="person-name"><strong>YOUR</strong> NAME</div>
    <div class="job-title">Your Job Title</div>
    <ul class="contact-list">
      <li>
        <svg viewBox="0 0 8 8"><path d="M4 0.5a2.3 2.3 0 0 1 2.3 2.3C6.3 4.5 4 7.5 4 7.5S1.7 4.5 1.7 2.8A2.3 2.3 0 0 1 4 0.5z" fill="var(--accent)"/><circle cx="4" cy="2.8" r="0.9" fill="#fff"/></svg>
        <b>Address:</b> 48 Harbor Works Lane, Millbrook, NY 11520
      </li>
      <li>
        <svg viewBox="0 0 8 8"><path d="M1.5 0.8l1.5 0 0.6 1.8-1 0.7c0.4 1 1.1 1.7 2.1 2.1l0.7-1 1.8 0.6 0 1.5c-3.3 0.3-6-2.4-5.7-5.7z" fill="var(--accent)"/></svg>
        <b>Tell:</b> (555) 014-2730
      </li>
      <li>
        <svg viewBox="0 0 8 8"><rect x="2" y="0.8" width="4" height="2.4" fill="var(--accent)"/><rect x="0.6" y="3" width="6.8" height="4.2" rx="0.6" fill="var(--accent)"/><rect x="2.2" y="4.4" width="3.6" height="1.2" fill="#fff"/></svg>
        <b>Fax:</b> (555) 014-2731
      </li>
      <li>
        <svg viewBox="0 0 8 8"><circle cx="4" cy="4" r="3.2" fill="none" stroke="var(--accent)" stroke-width="1.1"/><circle cx="4" cy="4" r="1.2" fill="var(--accent)"/></svg>
        <b>Email:</b> info@brellstone-example.com
      </li>
      <li>
        <svg viewBox="0 0 8 8"><circle cx="4" cy="4" r="2.6" fill="var(--accent)"/></svg>
        <b>social page</b>
      </li>
    </ul>
  </section>
</body>
</html>
```